Kumori Grill Sushi & Sake House

We need business card size flyer that will show our restaurant Logo (attached) with some sushi pictures and our address and phone number.
The flyer is specifically for 10% OFF all Alchohol beverage. Its a japanese sushi house so if you have some extra ideas to spice up the look, please advise.
Also the Address is:
418 W Larkmont Ave
Pasadena CA 91342

Phone number: 626-305-8824

```html
<!DOCTYPE html>
<html lang="en">
<head>
<meta charset="utf-8">
<title>Kumori Grill – Cards</title>
<link rel="stylesheet" href="https://fonts.googleapis.com/css2?family=PT+Sans+Narrow:wght@400;700&family=Open+Sans:wght@400&family=Fira+Sans+Extra+Condensed:ital,wght@0,400;1,400&display=swap">
<style>
  :root {
    --backdrop: #efe7de;
    --card: #fdeef2;
    --maroon: #951c45;
    --maroon-soft: #b5587a;
    --gold: #c9960f;
    --peach: #e8a47c;
    --frame: #eab495;
    --ink: #1d1a1a;
    --photo-soup: #5a3a26;
    --photo-sashimi: #c4486f;
    --photo-roll: #6b3d2a;
  }
  html, body {
    margin: 0;
    width: 1200px;
    height: 1200px;
    overflow: hidden;
    background: var(--backdrop);
  }
  .stage { position: relative; width: 1200px; height: 1200px; }
  .card {
    position: absolute;
    background: var(--card);
    border-radius: 0 38px 0 38px;
    overflow: hidden;
    box-shadow: 0 2px 6px rgba(0,0,0,.12);
  }
  .card--front { left: 45px; top: 80px; width: 535px; height: 935px; }
  .card--back { left: 632px; top: 200px; width: 535px; height: 933px; }

  .brand-name {
    position: absolute;
    font-family: "PT Sans Narrow", sans-serif;
    font-weight: 700;
    color: var(--maroon);
    margin: 0;
    white-space: nowrap;
  }
  .card--front .brand-name { left: 0; right: 0; top: 95px; text-align: center; font-size: 44px; line-height: 1; }
  .tagline { position: absolute; margin: 0; white-space: nowrap; }
  .card--front .tagline {
    left: 0; right: 0; top: 153px; text-align: center;
    font-family: "PT Sans Narrow", sans-serif; font-size: 27px; color: var(--maroon);
  }
  .card--front .tagline .accent { color: var(--peach); }

  .photo-grid { position: absolute; left: 0; top: 0; width: 535px; height: 935px; }
  .web-address { font-family: "PT Sans Narrow", sans-serif; font-size: 23px; fill: var(--ink); letter-spacing: .3px; }

  .contact {
    position: absolute; left: 0; right: 0; top: 784px; text-align: center;
    font-family: "PT Sans Narrow", sans-serif; font-size: 27px; line-height: 33px; color: var(--ink);
  }
  .contact p { margin: 0; }
  .contact svg { vertical-align: -4px; margin-right: 6px; }

  .card--back .brand-name { left: 62px; top: 170px; font-size: 92px; line-height: 1; }
  .card--back .tagline {
    left: 51px; top: 348px;
    font-family: "Open Sans", sans-serif; font-size: 28px; color: var(--ink);
  }
  .card--back .tagline .accent { color: var(--maroon); }

  .offer {
    position: absolute; left: 51px; right: 51px; top: 420px;
    border-top: 4px solid var(--gold);
    border-bottom: 4px solid var(--gold);
    padding: 10px 0 14px;
    text-align: center;
  }
  .offer-amount {
    margin: 0;
    font-family: "PT Sans Narrow", sans-serif; font-weight: 700;
    font-size: 120px; line-height: 1; color: var(--gold);
  }
  .offer-detail {
    margin: 4px 0 0;
    font-family: "Fira Sans Extra Condensed", sans-serif;
    font-size: 30px; line-height: 34px; color: var(--maroon);
  }

  .services {
    position: absolute; right: 118px; text-align: right;
    font-family: "Fira Sans Extra Condensed", sans-serif; font-size: 26px; line-height: 30px; color: var(--maroon);
  }
  .services p { margin: 0; }
  .services .note { font-style: italic; color: var(--maroon-soft); }
  .services--catering { top: 685px; }
  .services--sake { top: 790px; }
</style>
</head>
<body>
<div class="stage">

  <section class="card card--front">
    <h1 class="brand-name">Kumori Grill</h1>
    <p class="tagline">extraordinary <span class="accent">sushi &amp; sake</span></p>

    <svg class="photo-grid" viewBox="0 0 535 935">
      <g stroke="var(--frame)" stroke-width="8">
        <polygon role="img" aria-label="Photo of a bowl of Japanese soup with garnish"
                 points="65,167 253,355 65,543 -123,355" fill="var(--photo-soup)"/>
        <polygon role="img" aria-label="Photo of a plate of tuna sashimi with wasabi"
                 points="470,172 658,360 470,548 282,360" fill="var(--photo-sashimi)"/>
        <polygon role="img" aria-label="Photo of a sushi roll topped with tobiko beside sake glasses"
                 points="265,372 453,560 265,748 77,560" fill="var(--photo-roll)"/>
      </g>
      <text class="web-address" transform="translate(284 755) rotate(-45)">www.kumorigrillpasadena.com</text>
    </svg>

    <div class="contact">
      <p>418 W Larkmont Ave</p>
      <p>Pasadena, CA 91342</p>
      <p><svg width="26" height="26" viewBox="0 0 26 26" aria-hidden="true">
        <circle cx="13" cy="13" r="11.5" fill="none" stroke="var(--ink)" stroke-width="1.6"/>
        <path d="M9 7 c-2 2 -1 7 3 11 c3 2 5 2 6 1 l-2 -3 l-2 1 c-2 -1 -4 -4 -4 -6 l2 -1 z" fill="var(--ink)"/>
      </svg>626.305.8824</p>
    </div>
  </section>

  <section class="card card--back">
    <h2 class="brand-name">Kumori Grill</h2>
    <p class="tagline">extraordinary <span class="accent">sushi &amp; sake</span></p>

    <div class="offer">
      <p class="offer-amount">10% OFF</p>
      <p class="offer-detail">all alcoholic beverages</p>
    </div>

    <div class="services services--catering">
      <p>CATERING</p>
      <p>available for all occasions</p>
      <p class="note">Corporate discounts available</p>
    </div>
    <div class="services services--sake">
      <p>SAKE events</p>
      <p class="note">Sake Academy West</p>
      <p>Sake Pairing</p>
      <p>Sake Tasting</p>
    </div>
  </section>

</div>
</body>
</html>
```